Verodex business card

Business card for sustainable investment company called "Verodex". Verodex is an exchange platform selling carbon credits between buyers and sellers. Carbon Credits are an environmental commodity for reducing global carbon emissions.

the card should obviously have our logo and the theme should be sustainability/environment mixed with a trading platform.

Contact Information for Business Card

Logo, Name, Title, Phone, Email

Colors
0054AA
0677BA
7BADD7
CADEEF
E8F1F8
0094D4
00A9DD
6FCCEA
C7EBF8
E9F6FB
00AB8E
00BBA5
67D7C9
C6EFE9
E9F9F6
59FF00
82FF00
B8FF75
E3FFCB
F4FFEA

```html
<!DOCTYPE html>
<html lang="en">
<head>
<meta charset="utf-8">
<title>Verodex business card</title>
<link rel="stylesheet" href="https://fonts.googleapis.com/css2?family=Montserrat:wght@500;600;700&family=Open+Sans:wght@400;500&display=swap">
<style>
  :root {
    --navy: #1b2b57;
    --navy-deep: #14224a;
    --blue: #0677ba;
    --sky: #00a9dd;
    --aqua: #6fccea;
    --white: #ffffff;
    --ink: #1e2a44;
    --bg: #e9edf2;
  }
  * { box-sizing: border-box; margin: 0; padding: 0; }
  html, body { width: 1200px; height: 960px; overflow: hidden; }
  body {
    background: var(--bg);
    font-family: "Open Sans", sans-serif;
    position: relative;
  }
  .card {
    position: absolute;
    left: 250px;
    width: 700px;
    height: 400px;
    border-radius: 18px;
    overflow: hidden;
    box-shadow: 0 10px 30px rgba(20, 34, 74, 0.18);
  }
  .card-front {
    top: 50px;
    background: linear-gradient(160deg, #22335f 0%, var(--navy) 45%, var(--navy-deep) 100%);
  }
  .card-back {
    top: 510px;
    background: var(--white);
  }
  .wordmark {
    position: absolute;
    display: flex;
    align-items: center;
    gap: 22px;
  }
  .wordmark-square {
    width: 62px;
    height: 62px;
    background: var(--sky);
    border-radius: 6px;
  }
  .wordmark-name {
    font-family: "Montserrat", sans-serif;
    font-weight: 600;
    font-size: 64px;
    letter-spacing: 1px;
    line-height: 1;
  }
  .card-front .wordmark { left: 140px; top: 168px; }
  .card-front .wordmark-name { color: var(--white); }
  .card-back .wordmark { left: 212px; top: 70px; gap: 20px; }
  .card-back .wordmark-square { width: 54px; height: 54px; }
  .card-back .wordmark-name { color: var(--navy); font-size: 56px; }
  .identity {
    position: absolute;
    left: 150px;
    top: 176px;
    width: 220px;
    text-align: right;
  }
  .person-name {
    font-family: "Montserrat", sans-serif;
    font-weight: 700;
    font-size: 25px;
    white-space: nowrap;
  }
  .person-first { color: var(--sky); }
  .person-last { color: var(--navy); }
  .person-title {
    font-size: 18px;
    color: var(--ink);
    margin-top: 4px;
  }
  .divider {
    position: absolute;
    left: 386px;
    top: 160px;
    width: 2px;
    height: 92px;
    background: var(--sky);
  }
  .contact-list {
    position: absolute;
    left: 404px;
    top: 160px;
    list-style: none;
  }
  .contact-item {
    display: flex;
    align-items: center;
    gap: 10px;
    font-size: 18px;
    color: var(--ink);
    height: 30px;
  }
  .contact-item svg { width: 18px; height: 18px; flex: none; }
  .card-bands { position: absolute; inset: 0; width: 700px; height: 400px; }
  .social-handle {
    position: absolute;
    left: 540px;
    top: 328px;
    font-size: 22px;
    color: var(--white);
  }
</style>
</head>
<body>
  <section class="card card-front" aria-label="Card front">
    <div class="wordmark">
      <span class="wordmark-square"></span>
      <span class="wordmark-name">VERODEX</span>
    </div>
  </section>

  <section class="card card-back" aria-label="Card back">
    <svg class="card-bands" viewBox="0 0 700 400" aria-hidden="true">
      <defs>
        <linearGradient id="bandGradient" x1="0" y1="1" x2="1" y2="0">
          <stop offset="0" stop-color="#6fccea"/>
          <stop offset="0.5" stop-color="#00a9dd"/>
          <stop offset="1" stop-color="#3f78c8"/>
        </linearGradient>
      </defs>
      <polygon points="0,344 486,280 486,287 0,351" fill="#1b2b57"/>
      <polygon points="0,358 486,294 474,400 0,400" fill="url(#bandGradient)"/>
      <polygon points="500,272 700,246 700,400 486,400" fill="#1b2b57"/>
    </svg>

    <div class="wordmark">
      <span class="wordmark-square"></span>
      <span class="wordmark-name">VERODEX</span>
    </div>

    <div class="identity">
      <p class="person-name"><span class="person-first">DANIEL</span> <span class="person-last">MARSH</span></p>
      <p class="person-title">Co-Founder</p>
    </div>

    <span class="divider"></span>

    <ul class="contact-list">
      <li class="contact-item">
        <svg viewBox="0 0 24 24"><path fill="#0094d4" d="M6.6 10.8a15 15 0 0 0 6.6 6.6l2.2-2.2a1 1 0 0 1 1-.25 11.4 11.4 0 0 0 3.6.57 1 1 0 0 1 1 1V20a1 1 0 0 1-1 1A17 17 0 0 1 3 4a1 1 0 0 1 1-1h3.5a1 1 0 0 1 1 1c0 1.25.2 2.45.57 3.57a1 1 0 0 1-.25 1z"/></svg>
        555-210-4836
      </li>
      <li class="contact-item">
        <svg viewBox="0 0 24 24"><rect x="2" y="5" width="20" height="14" rx="2" fill="#0094d4"/><path d="M3 6l9 7 9-7" fill="none" stroke="#fff" stroke-width="1.6"/></svg>
        info@verodex.com
      </li>
      <li class="contact-item">
        <svg viewBox="0 0 24 24"><circle cx="12" cy="12" r="10" fill="#0094d4"/><path d="M2 12h20M12 2c3 3 3 17 0 20M12 2c-3 3-3 17 0 20" fill="none" stroke="#fff" stroke-width="1.4"/></svg>
        www.verodex.com
      </li>
    </ul>

    <p class="social-handle">@verodex.com</p>
  </section>
</body>
</html>
```